Web design for business website

I need a web design for a business website for one of our clients who is specialized in alarm management software. I would like you to design 3 web pages, one for each of the 3 pages. You need to process the corporate identity of our client to the web design. This means the colors of the logo (red and black) should definitely show up on all of the 3 pages. Find the logo file for the logo of our customer. To increase readability I suggest you use a white/light background. All suggestions are welcome.

Please kindly download atttached Webdesign.zip and read the project brief first. The project brief refers to all other files of the zip file. Your design must have exactly the same structure as the wireframes.
Updates

Target Market(s)

B2B, Alarm management

Industry/Entity Type

Business

Number of Pages Required

3 page

Requirements
Must have
• The web design must have exactly the same structure as the wireframes and needs to contain the colors of the company logo.

```html
<!DOCTYPE html>
<html lang="en">
<head>
<meta charset="utf-8">
<title>Verantis – Real-time reasoning solutions</title>
<link href="https://fonts.googleapis.com/css2?family=Open+Sans:wght@400;600;700&display=swap" rel="stylesheet">
<style>
:root{
  --accent:#e8461b;
  --ink:#1a1a1a;
  --navy:#1d1b34;
  --topbar:#141414;
  --light:#f4f4f4;
  --text:#666;
  --footer:#161616;
  --footer-text:#3f3f3f;
}
*{margin:0;padding:0;box-sizing:border-box}
html,body{width:689px;height:1200px;overflow:hidden;background:#fff;font-family:"Open Sans",sans-serif;color:var(--text)}
.wrap{position:relative;width:689px;height:1200px}
.topbar{height:19px;background:var(--topbar);display:flex;align-items:center;justify-content:space-between;padding:0 56px;font-size:7px;color:#ccc}
.topbar .right{display:flex;align-items:center;gap:5px;font-size:5.5px}
.lang-btn{width:14px;height:12px;background:var(--accent)}
.lang{width:35px;height:12px;background:#2a2a2a;color:#bbb;text-align:center;line-height:12px;font-size:6px}
.search{display:flex;height:12px}
.search span{width:68px;background:#2a2a2a;color:#888;padding-left:8px;line-height:12px;font-size:5px}
.search i{width:17px;background:var(--accent)}
.header{height:50px;background:#f7f7f7;display:flex;align-items:center;justify-content:space-between;padding:0 56px}
.brand{display:flex;flex-direction:column;line-height:1}
.brand b{font-size:20px;font-weight:600;color:var(--ink)}
.brand small{font-size:5.5px;color:#333;margin-top:2px}
.actions{display:flex;gap:7px}
.actions a{height:25px;font-size:6px;line-height:25px;background:#ddd;color:#666;border:1px solid #ccc;text-decoration:none;text-align:center}
.actions a.primary{background:var(--accent);color:#fff;border-color:var(--accent);width:70px}
.actions a.login{width:60px}.actions a.signup{width:69px}
.nav{height:24px;background:var(--navy);padding-left:56px;display:flex}
.nav a{color:#fff;font-size:6.5px;font-weight:600;text-decoration:none;line-height:24px;width:64px;text-align:center}
.nav a.active{background:var(--accent);width:49px;margin-right:2px}
.hero{position:relative;height:246px;background:linear-gradient(180deg,#8a8f94 0%,#c9a070 40%,#e0a04a 55%,#6a6a4a 75%,#3e4a2c 100%)}
.hero-box{position:absolute;left:190px;top:52px;width:310px;height:142px;background:rgba(255,255,255,.8);padding:18px 22px}
.hero-box h3{font-size:11px;font-weight:400;color:var(--ink)}
.hero-box h1{font-size:28px;font-weight:600;color:var(--accent);line-height:28px}
.hero-box h1 span{font-size:8.5px;font-weight:400;color:#333;margin-left:4px}
.hero-box p{font-size:5.5px;line-height:8.5px;color:#444;margin-top:6px;width:250px}
.btn{display:inline-block;background:var(--accent);color:#fff;font-size:6.5px;font-weight:600;text-decoration:none;text-align:center;box-shadow:0 2px 0 #b8330f}
.hero-box .btn{width:78px;height:24px;line-height:24px;margin-top:14px}
.arrow{position:absolute;top:101px;width:29px;height:29px;display:flex;align-items:center;justify-content:center}
.arrow.prev{left:27px;background:#eee}.arrow.next{right:27px;background:var(--accent)}
.welcome{height:103px;display:flex;align-items:center;justify-content:center;gap:5px;color:var(--ink)}
.welcome .t1{font-size:13px}.welcome .t2{font-size:30px;font-weight:600;color:var(--accent)}.welcome .t3{font-size:9px;color:#333;margin-top:6px}
.about{height:246px;background:var(--light);position:relative}
.about-text{position:absolute;left:57px;top:36px;width:280px}
.about h2{font-size:17px;font-weight:600;color:var(--accent)}
.about p{font-size:6.5px;line-height:9.7px;margin-top:10px}
.about .btn{width:79px;height:26px;line-height:26px;margin-top:14px}
.about-photo{position:absolute;left:352px;top:0;width:280px;height:246px;background:linear-gradient(160deg,#9fb0c2,#3b4a6a 60%,#2a3050)}
.clients-head{height:100px;text-align:center;padding-top:36px}
.clients-head h2{display:inline-block;font-size:14px;font-weight:600;color:var(--accent);border-bottom:1px solid #ccc;padding:0 38px 3px}
.clients-head p{font-size:8px;margin-top:6px}
.logos{height:50px;border-top:1px solid #ddd;border-bottom:1px solid #ddd;display:flex;align-items:center;justify-content:space-around;padding:0 60px}
.logos span{font-size:10px;font-weight:600;color:#3a3a3a}
.connect{position:absolute;top:881px;left:0;width:689px;height:123px;background:linear-gradient(180deg,#1c1c1c,#2a2418);padding:30px 56px;display:flex;gap:53px}
.connect h2{font-size:17px;font-weight:400;color:var(--accent)}
.socials{display:flex;gap:11px;margin-top:13px}
.socials i{width:25px;height:25px;background:#777}
.socials i.first{background:#3b5b9a}
.subscribe{display:flex;margin-top:13px;width:380px;height:25px;border:1px solid #fff}
.subscribe span{flex:1;background:#111;color:#fff;font-size:6.5px;line-height:23px;padding-left:14px}
.subscribe b{width:68px;background:#fff;color:var(--accent);font-size:6.5px;text-align:center;line-height:23px}
.footer{position:absolute;top:1004px;left:0;width:689px;height:166px;background:var(--footer);padding:36px 56px;display:flex}
.col{width:99px;font-size:6.5px;color:var(--footer-text);line-height:11px}
.col h4{font-size:8.5px;font-weight:400;margin-bottom:8px}
.col .hl{color:var(--accent)}
.col.contact{margin-left:49px;width:130px}
.col.contact div{display:flex;align-items:center;gap:8px;margin-bottom:5px}
.copy{position:absolute;top:1170px;left:0;width:689px;height:30px;background:var(--footer);border-top:1px solid #222;text-align:center;font-size:5.5px;line-height:30px;color:var(--footer-text)}
.copy b{color:var(--accent);font-weight:600}
</style>
</head>
<body>
<div class="wrap">
  <div class="topbar">
    <span>&#9742; +31 (0)20 555 0147</span>
    <div class="right">Selecte Language : <i class="lang-btn"></i><span class="lang">ENG</span><div class="search"><span>Search here...</span><i></i></div></div>
  </div>
  <header class="header">
    <div class="brand"><b>VERANTIS</b><small>Real-time reasoning solutions</small></div>
    <nav class="actions"><a class="primary" href="#">ACCOUNT</a><a class="login" href="#">LOG IN</a><a class="signup" href="#">SIGN UP</a></nav>
  </header>
  <nav class="nav"><a class="active" href="#">HOME</a><a href="#">INDUSTRY</a><a href="#">TELECOM</a><a href="#">POWER</a><a href="#">UTILITIES</a><a href="#">INFRA</a><a href="#">STORE</a></nav>
  <section class="hero" role="img" aria-label="Refinery at sunset beside a marsh">
    <div class="arrow prev"><svg width="6" height="8" viewBox="0 0 6 8"><path d="M5 0.5L1.5 4 5 7.5" stroke="#e8461b" stroke-width="1.6" fill="none"/></svg></div>
    <div class="arrow next"><svg width="6" height="8" viewBox="0 0 6 8"><path d="M1 0.5L4.5 4 1 7.5" stroke="#fff" stroke-width="1.6" fill="none"/></svg></div>
    <div class="hero-box">
      <h3>HELLO WE ARE</h3>
      <h1>VERANTIS<span>Real-time reasoning solutions</span></h1>
      <p>Companies have invested to get data out of processes. New technologies have been developed to get real-time data out of the harshest places, like oil-well drill heads or the Great Barrier Riff.</p>
      <a class="btn" href="#">READ MORE</a>
    </div>
  </section>
  <section class="welcome"><span class="t1">WELCOME TO</span><span class="t2">VERANTIS</span><span class="t3">Real-time reasoning solutions</span></section>
  <section class="about">
    <div class="about-text">
      <h2>ABOUT US</h2>
      <p>Companies have invested to get data out of processes. New technologies have been developed to get real-time data out of the harshest places, like oil-well drill heads or the Great Barrier Riff. Data in itself means nothing without the context the data is collected in. Example: data from equipment under maintenance does not provide information to operations. Information - data which is valid and meaningful can overwhelm any user without the proper knowledge to interpret this information.</p>
      <p>Verantis technology enables easy application of such knowledge in a comprehensible – visual – representation and makes hypothetical reasoning with information possible providing meaningful advisories to subscribers when they need it or when it is required that they are made aware of a situation which requires their attention.</p>
      <a class="btn" href="#">LEARN MORE</a>
    </div>
    <div class="about-photo" role="img" aria-label="Two engineers in hard hats inspecting pipework at a plant"></div>
  </section>
  <section class="clients-head"><h2>CLIENTS THAT TRUST US</h2><p>Some of our clients that trust us, be shure to be one of them.</p></section>
  <section class="logos"><span>Quarlen</span><span>Norvique</span><span>Petrava</span><span>Dalcor</span><span>Brewmont</span><span>Oristo</span><span>Tidewell Oil</span></section>
  <section class="connect">
    <div><h2>FOLLOW US ON :</h2><div class="socials"><i class="first" aria-label="Social network"></i><i aria-label="Social network"></i><i aria-label="Social network"></i><i aria-label="Social network"></i><i aria-label="Video channel"></i></div></div>
    <div><h2>SUBSCRIBE NOW :</h2><div class="subscribe"><span>Enter Your Email Adress</span><b>SUBSCRIBE</b></div></div>
  </section>
  <footer class="footer">
    <div class="col"><h4>SOLUTIONS</h4><div class="hl">KAVO Alarm Reporting</div><div>KAVO Alarm Analysis</div><div>KAVO Alarm Expert</div><div>USE</div></div>
    <div class="col"><h4>INDUSTRIES</h4><div>Industry</div><div>Telecom</div><div>Power</div><div>Utilites</div><div>Infra</div></div>
    <div class="col"><h4>ABOUT US</h4><div>Company</div><div>Overview</div><div>Leadership</div><div>Partners</div><div>Locations</div></div>
    <div class="col"><h4>NEWS</h4><div>Product News</div><div>Partner News</div><div>Events</div><div>Press Releases</div><div>Vacancies</div></div>
    <div class="col contact"><h4>CONTACT US</h4>
      <div><svg width="7" height="7" viewBox="0 0 10 10"><path d="M2 0l2 2-1 2 3 3 2-1 2 2-2 2C4 10 0 6 0 2z" fill="#3f3f3f"/></svg>+31 (0)20 555 0147</div>
      <div><svg width="7" height="6" viewBox="0 0 10 8"><rect width="10" height="8" fill="#3f3f3f"/><path d="M0 0l5 4 5-4" stroke="#161616" fill="none"/></svg>hello@verantis.example</div>
      <div><svg width="6" height="8" viewBox="0 0 8 10"><path d="M4 10L1 5a3.5 3.5 0 1 1 6 0z" fill="#3f3f3f"/></svg>Kanaalweg 12, Harbourtown</div>
    </div>
  </footer>
  <div class="copy">Copyright © 2105 <b>VERANTIS.</b> All Rights Reserved.</div>
</div>
</body>
</html>
```